Professional and creative business card design for recruiting service providers

Our company supports German medium-sized companies in filling vacancies promptly. For this we use social media marketing and bring our customers into the visibility.

We want a professional but also creative design for our business cards.

Please look at lindqvar-staff.de to get an impression of our CI.

Target Market(s)

Small and medium-sized companies in Germany from the industry

Industry/Entity Type

Industrie, Handwerk

Contact Information for Business Card

Name, Position, Telefonnummer, Email, Website

Colors
EE7325
F08F49
F5BC92
FAE3D3
FDF4ED

Requirements
Must have
• A picture of the employee and in the style of www.lindqvar-staff.de

```html
<!DOCTYPE html>
<html lang="de">
<head>
<meta charset="utf-8">
<title>Lindqvar Staff – Visitenkarte</title>
<link rel="stylesheet" href="https://fonts.googleapis.com/css2?family=Montserrat:wght@700;800&family=Arimo:wght@400;700&display=swap">
<style>
  :root {
    --orange: #e85a2b;
    --orange-deep: #c9461c;
    --orange-light: #f08f49;
    --orange-pale: #f5bc92;
    --ink: #2b2b2b;
    --grey-text: #3c3c3c;
    --paper: #ffffff;
    --backdrop: #e6e6e6;
    --suit-dark: #1d1e26;
    --photo-grey: #c9c9c9;
  }
  * { box-sizing: border-box; margin: 0; padding: 0; }
  html, body {
    width: 1200px; height: 802px; overflow: hidden;
    background: var(--backdrop);
  }
  .stage {
    width: 1200px; height: 802px;
    display: flex; align-items: center; justify-content: center; gap: 40px;
  }
  .card {
    width: 540px; height: 310px;
    position: relative; overflow: hidden;
    box-shadow: 0 10px 24px rgba(0,0,0,0.18);
  }
  /* Front */
  .card-front { background: var(--paper); }
  .portrait {
    position: absolute; right: 0; top: 0; width: 250px; height: 310px;
    background: linear-gradient(170deg, #d6d6d6 0%, var(--photo-grey) 35%, #4a4b55 60%, var(--suit-dark) 100%);
  }
  .card-content {
    position: absolute; left: 34px; top: 34px; width: 260px;
    font-family: "Arimo", Arial, sans-serif;
  }
  .brand { display: flex; align-items: center; gap: 12px; margin-bottom: 26px; }
  .brand-square { width: 34px; height: 34px; background: var(--orange); }
  .brand-name {
    font-family: "Montserrat", Arial, sans-serif; font-weight: 800;
    font-size: 19px; line-height: 1.05; letter-spacing: 0.5px; color: var(--ink);
  }
  .person-name {
    color: var(--orange); font-size: 17px; font-weight: 400;
    text-transform: uppercase; letter-spacing: 0.3px;
  }
  .person-role { color: var(--grey-text); font-size: 14px; margin-top: 2px; }
  .address { color: var(--grey-text); font-size: 13px; line-height: 1.35; margin-top: 18px; }
  .contact-list { list-style: none; margin-top: 16px; }
  .contact-list li {
    display: flex; align-items: center; gap: 9px;
    color: var(--grey-text); font-size: 13px; line-height: 1.5;
  }
  .contact-list svg { width: 11px; height: 11px; flex: none; }
  /* Back */
  .card-back {
    background:
      radial-gradient(ellipse 60% 70% at 85% 30%, rgba(245,188,146,0.35), transparent 70%),
      radial-gradient(ellipse 55% 60% at 20% 85%, rgba(240,143,73,0.30), transparent 70%),
      linear-gradient(160deg, var(--orange-deep) 0%, var(--orange) 35%, var(--orange) 65%, #ec6a36 100%);
  }
  .back-texture {
    position: absolute; inset: 0;
    background:
      linear-gradient(90deg, rgba(0,0,0,0.10) 0%, transparent 30%),
      linear-gradient(0deg, rgba(0,0,0,0.06) 0%, transparent 40%);
  }
  .back-brand {
    position: absolute; left: 330px; top: 140px;
    display: flex; align-items: center; gap: 10px;
  }
  .back-square { width: 22px; height: 22px; background: #ffffff; }
  .back-name {
    font-family: "Montserrat", Arial, sans-serif; font-weight: 800;
    font-size: 17px; letter-spacing: 0.5px; color: #ffffff;
  }
</style>
</head>
<body>
<main class="stage">
  <section class="card card-front">
    <div class="portrait" role="img" aria-label="Portraitfoto des Mitarbeiters in dunklem Rollkragenpullover und Sakko"></div>
    <div class="card-content">
      <div class="brand">
        <span class="brand-square"></span>
        <span class="brand-name">LINDQVAR<br>STAFF</span>
      </div>
      <p class="person-name">Lukas Brenner</p>
      <p class="person-role">Manager</p>
      <p class="address">Lindenallee 42b<br>70173 Stuttgart</p>
      <ul class="contact-list">
        <li>
          <svg viewBox="0 0 12 12"><path fill="var(--orange)" d="M2.5 1l2 2.2-1 1.3c.7 1.5 1.6 2.4 3 3l1.3-1L10 8.5 9 10.6C5 10.3 1.7 7 1.4 3z"/></svg>
          0170 234 5178
        </li>
        <li>
          <svg viewBox="0 0 12 12"><rect x="1" y="2.5" width="10" height="7" fill="none" stroke="var(--orange)" stroke-width="1.3"/><path d="M1 2.5l5 4 5-4" fill="none" stroke="var(--orange)" stroke-width="1.3"/></svg>
          info@lindqvar-staff.de
        </li>
        <li>
          <svg viewBox="0 0 12 12"><circle cx="6" cy="6" r="5" fill="none" stroke="var(--orange)" stroke-width="1.2"/><ellipse cx="6" cy="6" rx="2.2" ry="5" fill="none" stroke="var(--orange)" stroke-width="1"/><path d="M1 6h10" stroke="var(--orange)" stroke-width="1"/></svg>
          www.lindqvar-staff.de
        </li>
      </ul>
    </div>
  </section>
  <section class="card card-back">
    <div class="back-texture" role="img" aria-label="Geprägtes Relief-Muster in Orangetönen über die gesamte Rückseite"></div>
    <div class="back-brand">
      <span class="back-square"></span>
      <span class="back-name">LINDQVAR STAFF</span>
    </div>
  </section>
</main>
</body>
</html>
```